AI Business Tools Landing Page

My web-based website builder (Pavlora.com) will be adding many new features in the very near future and I need an eye-catching landing page to promote these new products.

The page will have a primary section of the 8 main products we are promoting:
1. AI Instant Website Generator
2. AI Chatbot
3. Online Store Builder with AI Assistance
4. AI Auto-Blogging System
5. Online Scheduling System
6. Custom Email System
7. SEO Service
8. CRM System

The page will also have a smaller section for links to our affiliate programs. These can be smaller, less-promanent buttons or links. These are the affiliate products:
1. Get Your LLC
2. Website Design and Maintenance
3. Search Ads Management
4. Social Media Posting Service
5. Logo Design
6. Trademark Registration
7. Patent Application
8. Printing Services (including postcards, flyers, and merch.)
9. Bulk AI Content Generator

The theme and color scheme of the page should follow the theme of our main website, which is https://pavlora.com.

I need the page fully coded and ready to deploy on my server.

I look forward to seeing your amazing designs!

```html
<!DOCTYPE html>
<html lang="en">
<head>
<meta charset="utf-8">
<title>Pavlora – AI Business Tools</title>
<link href="https://fonts.googleapis.com/css2?family=Inter:wght@400;500;600;700;800&display=swap" rel="stylesheet">
<style>
:root{
  --navy:#0c1a3d;
  --navy-2:#14285a;
  --blue:#2f6bff;
  --blue-soft:#e7eeff;
  --ink:#10172a;
  --muted:#5b6478;
  --line:#e3e7ef;
  --panel:#f2f4f8;
  --white:#ffffff;
}
*{box-sizing:border-box;margin:0;padding:0}
html,body{width:1200px;height:3076px;overflow:hidden}
body{font-family:"Inter",sans-serif;color:var(--ink);background:var(--white);position:relative;font-size:11px;line-height:1.5}
.col{position:absolute;top:0;overflow:hidden}
.col-intro{left:0;width:410px;height:1500px}
.col-services{left:420px;width:380px;height:3076px;background:var(--panel);padding:24px 22px}
.col-advantage{left:810px;width:200px;height:3076px}
.col-side{left:1020px;width:180px;height:3076px}
.btn{display:inline-block;background:var(--blue);color:var(--white);font-weight:600;font-size:10px;padding:7px 14px;border-radius:4px}
.btn-ghost{display:inline-block;border:1px solid var(--white);color:var(--white);font-weight:600;font-size:10px;padding:6px 13px;border-radius:4px}
.eyebrow{color:var(--blue);font-weight:600;font-size:10px;margin-bottom:6px}
.muted{color:var(--muted)}
.accent{color:var(--blue)}

/* intro column */
.hero{background:var(--navy);color:var(--white);height:150px;padding:26px 24px}
.hero h1{font-size:17px;font-weight:700;margin-bottom:16px}
.signup{display:flex;gap:6px}
.signup .field{flex:1;height:30px;background:var(--white);border-radius:4px;color:#8a93a6;font-size:10px;padding:8px 10px}
.signup .btn{height:30px}
.intro{padding:24px 24px}
.intro h2{font-size:13px;font-weight:700;margin-bottom:8px}
.intro .big{font-size:26px;font-weight:800;line-height:1.15;margin-bottom:14px}
.intro p{font-size:10.5px;color:var(--muted);margin-bottom:12px}
.art{border-radius:8px}
.intro .art{height:120px;margin:18px 0;background:radial-gradient(circle at 50% 50%,#2f6bff 0,#14285a 45%,#f3f5f9 46%)}
.intro .lead{font-size:19px;font-weight:800;line-height:1.25;margin-bottom:12px}
.features{padding:0 24px}
.feature{display:flex;gap:12px;margin-bottom:22px}
.feature .ico{flex:0 0 32px;height:32px;border-radius:50%;background:var(--navy);display:flex;align-items:center;justify-content:center}
.feature h3{font-size:12px;font-weight:700;margin-bottom:3px}
.feature p{font-size:10px;color:var(--muted)}

/* services column */
.services-head h2{font-size:26px;font-weight:800;line-height:1.15;margin-bottom:10px}
.services-head p{font-size:10.5px;color:var(--muted);margin-bottom:14px}
.service{background:var(--white);border-radius:8px;padding:26px 26px 20px;margin-top:18px}
.service h3{font-size:27px;font-weight:800;line-height:1.12;margin-bottom:16px;text-align:center}
.service ul{list-style:none}
.service li{display:flex;gap:10px;font-size:10.5px;color:var(--muted);margin-bottom:12px}
.service li svg{flex:0 0 14px;margin-top:2px}
.service .more{font-size:10.5px;font-weight:600;color:var(--ink);margin-top:4px}

/* advantage column */
.adv{padding:22px 10px 0}
.adv h2{font-size:22px;font-weight:800;line-height:1.15;margin-bottom:10px}
.adv > p{font-size:9.5px;color:var(--muted);margin-bottom:14px}
.adv .art-phone{height:150px;margin-bottom:18px;background:linear-gradient(140deg,#dfe8ff,#2f6bff 60%,#14285a)}
.adv-item{margin-bottom:14px}
.adv-item h3{font-size:10px;font-weight:700;margin-bottom:2px}
.adv-item p{font-size:9px;color:var(--muted)}
.adv .art-laptop{height:150px;margin:10px 0 70px;background:linear-gradient(160deg,#eef2fa,#2f6bff 70%,#0c1a3d)}
.aff h2{font-size:22px;font-weight:800;line-height:1.15;margin-bottom:10px}
.aff > p{font-size:9.5px;color:var(--muted);margin-bottom:22px}
.aff-item{margin-bottom:22px}
.aff-item .ico{width:22px;height:22px;border-radius:50%;background:var(--navy);margin-bottom:8px;display:flex;align-items:center;justify-content:center}
.aff-item h3{font-size:12px;font-weight:700;line-height:1.25;margin-bottom:4px}
.aff-item p{font-size:9px;color:var(--muted)}
.cta{background:var(--navy);color:var(--white);padding:20px 14px}
.cta h2{font-size:20px;font-weight:800;line-height:1.15;margin-bottom:8px}
.cta p{font-size:9px;color:#c2cbe0;margin-bottom:12px}
.cta .row{display:flex;gap:6px}
.cta-bottom{position:absolute;left:10px;right:0;top:2720px;height:200px}

/* side column */
.cta-top{height:160px}
.testimonials{padding:140px 12px 0}
.testimonials h2{font-size:17px;font-weight:800;line-height:1.2;margin-bottom:14px}
.quote{border-top:1px solid var(--line);padding:10px 0}
.quote p{font-size:9px;color:var(--muted);margin-bottom:6px}
.quote .who{display:flex;gap:6px;align-items:center;font-size:9px;font-weight:600}
.quote .who span.dot{width:16px;height:16px;border-radius:50%;background:var(--blue-soft)}
.footer{position:absolute;top:820px;left:0;right:0;height:680px;background:var(--navy);color:var(--white);padding:20px 14px}
.brand{display:flex;align-items:center;gap:6px;font-size:13px;font-weight:700;margin-bottom:10px}
.brand i{width:12px;height:12px;background:var(--blue);border-radius:3px;display:block}
.footer p{font-size:8.5px;color:#aeb8d0;margin-bottom:16px}
.footer h4{font-size:10px;font-weight:700;margin:10px 0 6px}
.footer ul{list-style:none}
.footer li{font-size:9px;color:#c8d0e3;margin-bottom:5px;display:flex;align-items:center;gap:6px}
.footer li .s{width:10px;height:10px;border-radius:50%;border:1px solid #c8d0e3}
.footer .rule{border-top:1px solid #2a3a66;margin:12px 0}
</style>
</head>
<body>

<!-- Intro column -->
<section class="col col-intro">
  <header class="hero">
    <h1>The Premier AI Website Builder</h1>
    <div class="signup"><div class="field">Enter your email</div><span class="btn">Sign Up</span></div>
  </header>
  <div class="intro">
    <h2>Discover the Future of Website Creation with Pavlora!</h2>
    <p class="big">Your <span class="accent">FREE</span> Stunning Website in <span class="accent">1-Click</span> Built by Artificial Intelligence</p>
    <p>In the rapidly evolving digital era, the integration of artificial intelligence into web services is remarkably transformative. Pavlora, a pioneer in AI-driven design, gives you a polished, custom website built around your business in seconds, no coding or design skills needed. Simply tell us about your brand and watch the site take shape before your eyes.</p>
    <span class="btn">Start Your Free Website</span>
    <div class="art" role="img" aria-label="Illustration of the Pavlora AI builder emblem"></div>
    <p class="eyebrow">Why Choose Pavlora?</p>
    <p class="lead">Pavlora leverages AI technology to streamline the website creation process, making it faster, more efficient, and incredibly user-friendly. Here's what sets Pavlora apart:</p>
    <p>In the rapidly evolving digital era, the integration of artificial intelligence into web services is remarkably transformative. Pavlora blends smart automation with thoughtful design so every page you publish looks professional, loads quickly and grows with you.</p>
    <span class="btn">Build Your Site Now</span>
  </div>
  <div class="features">
    <div class="feature"><span class="ico"><svg width="14" height="14" viewBox="0 0 14 14"><path d="M8 1L3 8h4l-1 5 5-7H7z" fill="#fff"/></svg></span><div><h3>Instant Generation</h3><p>Pavlora can turn your ideas into a complete, ready-to-launch website in just seconds, saving time and effort.</p></div></div>
    <div class="feature"><span class="ico"><svg width="14" height="14" viewBox="0 0 14 14"><rect x="2" y="2" width="10" height="10" rx="2" fill="none" stroke="#fff" stroke-width="1.5"/></svg></span><div><h3>Unparalleled Flexibility</h3><p>Adjust layouts, colors, and content with ease. Every section of your new site stays fully editable.</p></div></div>
    <div class="feature"><span class="ico"><svg width="14" height="14" viewBox="0 0 14 14"><circle cx="7" cy="7" r="5" fill="none" stroke="#fff" stroke-width="1.5"/></svg></span><div><h3>Zero Cost to Start</h3><p>Launch your first website for free, then upgrade only when you need more power.</p></div></div>
    <div class="feature"><span class="ico"><svg width="14" height="14" viewBox="0 0 14 14"><path d="M2 8a5 5 0 0110 0v3H9V8M2 8v3h3V8" fill="none" stroke="#fff" stroke-width="1.5"/></svg></span><div><h3>Robust User Support</h3><p>Our friendly team and knowledge base are ready to help you every step of the way.</p></div></div>
  </div>
</section>

<!-- Services column -->
<section class="col col-services">
  <div class="services-head">
    <p class="eyebrow">Services</p>
    <h2>Explore Our Cutting-Edge AI Services</h2>
    <p>Unlock the potential of your business with our AI solutions. From instant website creation to smart customer tools, every service is designed to help you grow.</p>
    <span class="btn">Learn More</span>
  </div>

  <article class="service"><h3>AI Instant Website Generator</h3><ul>
    <li><svg width="14" height="14" viewBox="0 0 14 14"><path d="M2 7l3 3 7-7" fill="none" stroke="#2f6bff" stroke-width="2"/></svg>Get a professional, SEO-optimized website created in seconds.</li>
    <li><svg width="14" height="14" viewBox="0 0 14 14"><path d="M2 7l3 3 7-7" fill="none" stroke="#2f6bff" stroke-width="2"/></svg>Built-in CMS that lets integrate blogging, file hosting, and custom pages.</li></ul>
    <p class="more">Learn More ›</p></article>

  <article class="service"><h3>Intelligent AI ChatBot Service</h3><ul>
    <li><svg width="14" height="14" viewBox="0 0 14 14"><path d="M2 7l3 3 7-7" fill="none" stroke="#2f6bff" stroke-width="2"/></svg>Fully trainable chatbot to automate the customer support process.</li>
    <li><svg width="14" height="14" viewBox="0 0 14 14"><path d="M2 7l3 3 7-7" fill="none" stroke="#2f6bff" stroke-width="2"/></svg>Answers visitor questions day and night in your own brand voice.</li></ul>
    <p class="more">Learn More ›</p></article>

  <article class="service"><h3>AI Assistance for Online Store Builder</h3><ul>
    <li><svg width="14" height="14" viewBox="0 0 14 14"><path d="M2 7l3 3 7-7" fill="none" stroke="#2f6bff" stroke-width="2"/></svg>Sell your products online and integrate AI assistance easily.</li>
    <li><svg width="14" height="14" viewBox="0 0 14 14"><path d="M2 7l3 3 7-7" fill="none" stroke="#2f6bff" stroke-width="2"/></svg>Accept payments from multiple payment gateways including direct transfers.</li></ul>
    <p class="more">Learn More ›</p></article>

  <article class="service"><h3>AI Auto-Blogging System</h3><ul>
    <li><svg width="14" height="14" viewBox="0 0 14 14"><path d="M2 7l3 3 7-7" fill="none" stroke="#2f6bff" stroke-width="2"/></svg>Generate an AI-created blog post and publish to your domain.</li>
    <li><svg width="14" height="14" viewBox="0 0 14 14"><path d="M2 7l3 3 7-7" fill="none" stroke="#2f6bff" stroke-width="2"/></svg>Set your theme, weekly or monthly posts and forget it.</li></ul>
    <p class="more">Learn More ›</p></article>

  <article class="service"><h3>Online Scheduling System</h3><ul>
    <li><svg width="14" height="14" viewBox="0 0 14 14"><path d="M2 7l3 3 7-7" fill="none" stroke="#2f6bff" stroke-width="2"/></svg>Get appointments scheduled directly from your website.</li>
    <li><svg width="14" height="14" viewBox="0 0 14 14"><path d="M2 7l3 3 7-7" fill="none" stroke="#2f6bff" stroke-width="2"/></svg>Manage your schedule from a simple, user-friendly dashboard.</li></ul>
    <p class="more">Learn More ›</p></article>

  <article class="service"><h3>Custom emails using your domain</h3><ul>
    <li><svg width="14" height="14" viewBox="0 0 14 14"><path d="M2 7l3 3 7-7" fill="none" stroke="#2f6bff" stroke-width="2"/></svg>Quickly set up your email with your own domain name in moments.</li>
    <li><svg width="14" height="14" viewBox="0 0 14 14"><path d="M2 7l3 3 7-7" fill="none" stroke="#2f6bff" stroke-width="2"/></svg>Manage all your inboxes in one place from your dashboard.</li></ul>
    <p class="more">Learn More ›</p></article>

  <article class="service"><h3>SEO Service – Automatic Backlink Building</h3><ul>
    <li><svg width="14" height="14" viewBox="0 0 14 14"><path d="M2 7l3 3 7-7" fill="none" stroke="#2f6bff" stroke-width="2"/></svg>Let us do the hard work of getting high-quality backlinks to your website.</li>
    <li><svg width="14" height="14" viewBox="0 0 14 14"><path d="M2 7l3 3 7-7" fill="none" stroke="#2f6bff" stroke-width="2"/></svg>Get 30 high-quality, relevant backlinks to your site each month.</li></ul>
    <p class="more">Learn More ›</p></article>

  <article class="service"><h3>Customer Relationship Management (CRM) System</h3><ul>
    <li><svg width="14" height="14" viewBox="0 0 14 14"><path d="M2 7l3 3 7-7" fill="none" stroke="#2f6bff" stroke-width="2"/></svg>Automate the lead follow-up process in favor of your business.</li>
    <li><svg width="14" height="14" viewBox="0 0 14 14"><path d="M2 7l3 3 7-7" fill="none" stroke="#2f6bff" stroke-width="2"/></svg>Automate emails and text messages to keep every client engaged.</li></ul>
    <p class="more">Learn More ›</p></article>
</section>

<!-- Advantage column -->
<section class="col col-advantage">
  <div class="adv">
    <h2>The <span class="accent">AI Advantage</span> in Website Building</h2>
    <p>Discover how AI-driven tools give your business an edge, from faster launches to smarter updates that keep your site fresh and effective.</p>
    <div class="art art-phone" role="img" aria-label="Illustration of a phone showing an AI-built website"></div>
    <div class="adv-item"><h3>Seamless Efficiency</h3><p>AI builds and updates pages in moments, freeing your time for growth.</p></div>
    <div class="adv-item"><h3>Cost-Efficiency</h3><p>Skip costly agencies and get professional results at a fraction of the price.</p></div>
    <div class="adv-item"><h3>Unlimited Flexibility</h3><p>Change layouts, content and style whenever your business evolves.</p></div>
    <div class="adv-item"><h3>Customization and Personalization</h3><p>Tailor every section to match your brand and your audience.</p></div>
    <div class="adv-item"><h3>Round-the-clock Operation</h3><p>Your site, chatbot and store keep working even while you sleep.</p></div>
    <div class="adv-item"><h3>Scalability</h3><p>Start small and add pages, products and tools as you grow.</p></div>
    <div class="art art-laptop" role="img" aria-label="Illustration of a laptop displaying a website dashboard"></div>
    <div class="aff">
      <p class="eyebrow">Empower</p>
      <h2>Unlock Your Business Potential with Our <span class="accent">Affiliate</span> Resources</h2>
      <p>Explore our curated range of affiliate services built to support your business at every stage, from launch and branding to marketing and printing.</p>
      <div class="aff-item"><span class="ico"><svg width="10" height="10" viewBox="0 0 10 10"><path d="M1 5l3 3 5-6" fill="none" stroke="#fff" stroke-width="1.6"/></svg></span><h3>Comprehensive Solutions for Your Business Needs</h3><p>Our partners are trusted to meet diverse business requirements.</p></div>
      <div class="aff-item"><span class="ico"><svg width="10" height="10" viewBox="0 0 10 10"><path d="M1 5l3 3 5-6" fill="none" stroke="#fff" stroke-width="1.6"/></svg></span><h3>Simplify Your Operations with Our Expert Services</h3><p>We streamline your processes so you can focus on what matters most.</p></div>
      <div class="aff-item"><span class="ico"><svg width="10" height="10" viewBox="0 0 10 10"><path d="M1 5l3 3 5-6" fill="none" stroke="#fff" stroke-width="1.6"/></svg></span><h3>Take Advantage of Our Affiliate Offerings Today</h3><p>Get started with valuable resources for your business.</p></div>
      <span class="btn">Learn More</span>
    </div>
  </div>
  <div class="cta cta-bottom">
    <h2>Experience the Future of AI</h2>
    <p>Unlock your business potential with our AI products and see the difference today.</p>
    <div class="row"><span class="btn">Sign Up</span><span class="btn-ghost">Learn More</span></div>
  </div>
</section>

<!-- Side column -->
<aside class="col col-side">
  <div class="cta cta-top">
    <h2>Experience the Future of AI</h2>
    <p>Unlock your business potential with our AI products and see the difference.</p>
    <div class="row"><span class="btn">Sign Up</span><span class="btn-ghost">Learn More</span></div>
  </div>
  <div class="testimonials">
    <h2>What Our Site Owners Says</h2>
    <div class="quote"><p>"My website was live in minutes and it looks amazing."</p><div class="who"><span class="dot"></span>Owner, Bakery</div></div>
    <div class="quote"><p>"The chatbot handles most of our customer questions now."</p><div class="who"><span class="dot"></span>Founder, Studio</div></div>
  </div>
  <footer class="footer">
    <div class="brand"><i></i>Pavlora</div>
    <p>AI web design tools and hosted sites built to help small businesses launch quickly and grow online.<br>© 2024 Pavlora. All Rights Reserved.</p>
    <h4>Navigation</h4>
    <ul><li>About Pavlora</li><li>Services</li><li>Pricing</li><li>Features</li><li>Blog</li><li>Sitemap</li></ul>
    <h4>Affiliate Program</h4>
    <ul>
      <li>Get Your LLC</li><li>Website Design and Maintenance</li><li>Search Ads Management</li><li>Social Media Posting Service</li><li>Logo Design</li><li>Trademark Registration</li><li>Patent Application</li><li>Printing Services</li><li>Bulk AI Content Generator</li>
    </ul>
    <div class="rule"></div>
    <h4>Follow Us</h4>
    <ul><li><span class="s"></span>Friendlink</li><li><span class="s"></span>Snapgrid</li><li><span class="s"></span>Postline</li><li><span class="s"></span>Worknet</li><li><span class="s"></span>Clipstream</li></ul>
    <div class="rule"></div>
    <ul><li>Privacy Policy</li><li>Terms of Service</li><li>https://pavlora.com</li></ul>
  </footer>
</aside>

</body>
</html>
```